New Payments Start-up requires Logo, Style Guide and Web Site Design

We need a logo, style guide (colour templates etc.) and marketing web-site (HTML/CSS styling) for Fenwu, a new account-to-account payment product for use in the Single European Payment Area (SEPA).

The design is for the product only, not a company brand. We're looking for basic palette and style guidelines also. The web site need only be a basic responsive cross-platform design and layout. We will produce our own content.

We have no requirements for specific colours or logo styles. It is a financial product, however, so should not appear too quirky or untrustworthy.

The product is still in the early phases of development, so we're not able to provide pictures or other content.

As a little more detail on how things work, though, our end customers will arrive at our site through redirection from our merchant partners (a number of whom are large multi-national companies) who have offered our services as an alternative to credit card payments. They will be able to set up a SEPA direct debit mandate online in just a few pages, secure that with a password and use it to pay both immediately and in future with a simple confirmation of the password… a quick, easy checkout.

Because we work with large customer in the payments space, whilst we’d like the brand to be modern and appealing, it has to engender trust and stability. Whilst this product is new and in start-up phase, our company has been in alternative payments for nearly 10 years and have strong products in Europe in the Pre-Paid Zelo/TrevinCard and Voucher space. We'd like to treat this separately, however, which is why we've briefed accordingly.

Reason: Apologies for the extension, but I had a couple of designers contact me to say they had completed work but were unable to submit because time ran out. I'll only extend this once, though, because we need to get cracking on the project. Many thanks Jem

Target Market(s)

European alternative payment customers

Industry/Entity Type

Financial

Logo Text

fenwu

Coding

Coded - Design and coding required

Number of Pages Required

1 page

Font styles to use
Sans Serif

```html
<!DOCTYPE html>
<html lang="en">
<head>
<meta charset="utf-8">
<title>Fenwu — Account-to-Account Payments</title>
<link rel="stylesheet" href="https://fonts.googleapis.com/css2?family=Roboto:wght@400;500&family=Open+Sans:wght@400;600;700&display=swap">
<style>
:root{
  --orange:#f0540f;
  --orange-dark:#d9420a;
  --blue:#1a8ad8;
  --blue-deep:#1479c2;
  --ink:#333;
  --muted:#7a7f85;
  --pale:#eef2f5;
  --dark:#2d2f33;
  --white:#fff;
}
*{box-sizing:border-box;margin:0;padding:0}
html,body{width:1200px;height:2778px;overflow:hidden}
body{font-family:"Open Sans",Arial,sans-serif;color:var(--ink);background:var(--white)}
h1,h2,h3,.brand{font-family:"Roboto",Arial,sans-serif;font-weight:400}
.btn{display:inline-block;background:var(--orange);color:var(--white);font-family:"Open Sans",Arial,sans-serif;font-weight:600;font-size:16px;text-decoration:none;border-radius:3px;border-bottom:3px solid var(--orange-dark)}
.wrap{width:980px;margin:0 auto;position:relative}

/* header */
.site-header{height:89px;display:flex;align-items:center}
.site-header .wrap{display:flex;align-items:center;justify-content:space-between}
.brand{font-size:44px;font-weight:500;color:var(--blue);letter-spacing:1px}
.main-nav{display:flex;align-items:center;gap:44px;font-size:13px}
.main-nav a{color:#444;text-decoration:none}
.main-nav a.active{color:var(--blue)}
.main-nav .btn{font-size:13px;padding:11px 30px 10px;display:flex;align-items:center;gap:7px}

/* hero */
.hero{height:524px;position:relative;background:linear-gradient(180deg,#6d6a68 0%,#86817d 45%,#5f5954 100%);color:var(--white);text-align:center}
.hero-photo{position:absolute;inset:0;background:radial-gradient(ellipse at 38% 55%,rgba(210,180,160,.45),transparent 55%),radial-gradient(ellipse at 55% 20%,rgba(230,230,230,.35),transparent 40%)}
.hero-copy{position:relative;padding-top:216px}
.hero-copy p{font-size:16px}
.hero-copy h1{font-size:40px;margin:10px 0 24px}
.hero-copy .btn{padding:19px 30px 17px}
.slider-dots{position:absolute;left:0;right:0;top:480px;display:flex;justify-content:center;gap:9px}
.slider-dots span{width:15px;height:15px;border-radius:50%;background:rgba(255,255,255,.6)}
.slider-dots span.on{background:var(--white);border:3px solid var(--blue)}

/* how it works */
.how{height:520px;background:var(--pale);text-align:center;padding-top:66px}
.section-title{font-size:31px;color:#333}
.lead{font-size:12px;line-height:29px;color:var(--muted);width:960px;margin:18px auto 0}
.steps{display:flex;justify-content:space-between;margin:26px auto 0;width:1000px;position:relative}
.steps::before{content:"";position:absolute;top:56px;left:170px;right:170px;border-top:6px dotted #ccd3d9}
.step{width:250px;position:relative}
.step-icon{width:112px;height:112px;border-radius:50%;margin:0 auto;background:var(--orange);border:6px solid #fde3d6;box-shadow:0 0 0 3px #fff inset;display:flex;align-items:center;justify-content:center}
.step h3{font-size:20px;margin:24px 0 10px}
.step p{font-size:12px;line-height:29px;color:var(--muted);width:220px;margin:0 auto}

/* why */
.why{height:537px;background:linear-gradient(135deg,var(--blue) 0%,var(--blue-deep) 100%);color:var(--white);padding-top:46px}
.why .section-title{color:var(--white);text-align:center}
.why .lead{color:var(--white);text-align:center;font-size:12px;margin-top:16px}
.features{display:grid;grid-template-columns:1fr 1fr;column-gap:40px;width:990px;margin:36px auto 0}
.feature{border-bottom:1px solid rgba(255,255,255,.2);padding-bottom:18px;margin-bottom:26px}
.feature h3{font-size:20px;display:flex;align-items:center;gap:8px;margin-bottom:12px}
.feature p{font-size:12px;line-height:29px}

/* partners */
.partners{height:232px;text-align:center;padding-top:48px}
.partner-row{display:flex;justify-content:space-between;width:1000px;margin:42px auto 0;align-items:center}
.partner-mark{width:100px;height:56px;border-radius:6px;background:#d6d9dc}
.partner-mark.round{width:78px;height:66px;border-radius:50%}

/* testimonials */
.testimonials{height:356px;background:var(--pale);padding-top:64px}
.testimonials .section-title{text-align:center}
.quotes{display:flex;justify-content:space-between;width:990px;margin:32px auto 0}
.quote{width:475px}
.quote-body{display:flex;gap:12px;border-bottom:1px solid #dde2e6;padding-bottom:12px}
.avatar{flex:none;width:96px;height:96px;border-radius:50%;border:4px solid #fff;box-shadow:0 1px 3px rgba(0,0,0,.2);background:linear-gradient(160deg,#c9ccd0,#4a4f57)}
.quote-body p{font-size:12px;line-height:29px;color:#8a8f94;text-align:justify}
.quote-by{font-size:12px;color:var(--muted);margin-top:12px}
.quote-by strong{color:var(--orange);font-size:14px;font-weight:700;margin-right:4px}

/* closing band */
.closing{height:410px;background:radial-gradient(ellipse at 50% 50%,#36393e,var(--dark) 70%);color:var(--white);text-align:center;padding-top:120px}
.closing p{font-size:16px}
.closing h2{font-size:31px;margin:14px 0 20px}
.card-row{display:flex;justify-content:center;gap:20px;margin-bottom:28px}
.card-chip{width:38px;height:24px;background:#6b6e73;border-radius:2px}
.closing .btn{padding:19px 31px 17px}

/* footer */
.site-footer{height:110px;background:var(--blue);color:var(--white)}
.site-footer .wrap{display:flex;align-items:center;height:110px}
.site-footer .brand{color:var(--white);font-size:40px;padding-right:22px;border-right:1px solid rgba(255,255,255,.4);line-height:64px}
.footer-meta{padding-left:20px;font-size:12px;line-height:28px}
.footer-meta a{color:var(--white);text-decoration:none;margin-right:8px}
.social{margin-left:auto;display:flex;gap:7px}
.social span{width:28px;height:28px;border-radius:50%;background:#e8ecef}
</style>
</head>
<body>

<header class="site-header">
  <div class="wrap">
    <div class="brand">Fenwu</div>
    <nav class="main-nav">
      <a class="active" href="#">Home</a>
      <a href="#">How it works</a>
      <a href="#">About Us</a>
      <a href="#">Contact Us</a>
      <a class="btn" href="#">
        <svg width="11" height="12" viewBox="0 0 11 12"><circle cx="5.5" cy="3" r="3" fill="#fff"/><path d="M0 12c0-4 2.5-5.5 5.5-5.5S11 8 11 12z" fill="#fff"/></svg>
        Signin
      </a>
    </nav>
  </div>
</header>

<section class="hero">
  <div class="hero-photo" role="img" aria-label="Photo of a hand holding a payment card while tapping a tablet"></div>
  <div class="hero-copy">
    <p>Account-to-Account payment product for use in the</p>
    <h1>Single European Payment Area</h1>
    <a class="btn" href="#">Get Started Now</a>
  </div>
  <div class="slider-dots"><span></span><span></span><span class="on"></span><span></span></div>
</section>

<section class="how">
  <h2 class="section-title">How It Works?</h2>
  <p class="lead">Lorem ipsum dolor sit amet, consectetur adipiscing elit. Cras non velit eu augue volutpat tempor ut a velit. Pellentesque egestas lacus id enim molestie, eget viverra velit rutrum. Nulla id elementum lacus. Aliquam erat volutpat. Nulla nec rutrum odio.</p>
  <div class="steps">
    <div class="step">
      <div class="step-icon"><svg width="34" height="36" viewBox="0 0 34 36"><circle cx="17" cy="10" r="9" fill="#fff"/><path d="M1 36c0-10 7-15 16-15s16 5 16 15z" fill="#fff"/></svg></div>
      <h3>Signup</h3>
      <p>Duis ligula metus, ornare vitae risus vitae, laoreet consequat felis. Suspen disse turpis enimph.</p>
    </div>
    <div class="step">
      <div class="step-icon"><svg width="32" height="38" viewBox="0 0 32 38"><path d="M8 17V11a8 8 0 0 1 16 0v6" fill="none" stroke="#fff" stroke-width="4"/><rect x="2" y="16" width="28" height="22" rx="3" fill="#fff"/><circle cx="16" cy="26" r="3" fill="#f0540f"/></svg></div>
      <h3>Get Secure Password</h3>
      <p>Duis ligula metus, ornare vitae risus vitae, laoreet consequat felis. Suspen disse turpis enimph.</p>
    </div>
    <div class="step">
      <div class="step-icon"><svg width="44" height="30" viewBox="0 0 44 30"><rect x="1" y="1" width="42" height="28" rx="2" fill="none" stroke="#fff" stroke-width="2.5"/><rect x="6" y="6" width="32" height="18" fill="#fff"/><circle cx="22" cy="15" r="6" fill="#f0540f"/><text x="22" y="19" font-size="10" font-family="Arial" font-weight="700" fill="#fff" text-anchor="middle">1</text></svg></div>
      <h3>Pay Payments</h3>
      <p>Duis ligula metus, ornare vitae risus vitae, laoreet consequat felis. Suspen disse turpis enimph.</p>
    </div>
    <div class="step">
      <div class="step-icon"><svg width="40" height="38" viewBox="0 0 40 38"><rect x="2" y="6" width="30" height="30" rx="4" fill="none" stroke="#fff" stroke-width="3.5"/><path d="M9 19l7 7L38 3" fill="none" stroke="#fff" stroke-width="5"/></svg></div>
      <h3>Easy Checkout</h3>
      <p>Duis ligula metus, ornare vitae risus vitae, laoreet consequat felis. Suspen disse turpis enimph.</p>
    </div>
  </div>
</section>

<section class="why">
  <h2 class="section-title">Why Choose Us?</h2>
  <p class="lead">Cras ac volutpat ipsum. Donec magna ex, placerat et blandit at, imperdiet quis neque. Vestibulum feugiat augue vitae velit ornare, vel auctor turpis vehicula. Suspendisse dictum accumsan risus a tempor. Morbi finibus nunc justo, eu consectetur elit auctor non.</p>
  <div class="features">
    <div class="feature">
      <h3><svg width="18" height="18" viewBox="0 0 18 18"><circle cx="9" cy="9" r="9" fill="#fff"/><path d="M5 9l3 3 5-6" fill="none" stroke="#1a8ad8" stroke-width="2.4"/></svg>Easy and Convenient</h3>
      <p>Phasellus nibh sapien, vulputate sit amet dui vitae, sodales posuere nisl. In hac habit asse platea dictumst. Vivamus ac dui mauris.</p>
    </div>
    <div class="feature">
      <h3><svg width="18" height="18" viewBox="0 0 18 18"><circle cx="9" cy="9" r="9" fill="#fff"/><path d="M5 9l3 3 5-6" fill="none" stroke="#1a8ad8" stroke-width="2.4"/></svg>Advanced Segmentation</h3>
      <p>Quisque sit amet diam ante. Cras ac volutpat ipsum. Donec magna ex, placerat et blandit at, imperdiet quis neque.</p>
    </div>
    <div class="feature">
      <h3><svg width="18" height="18" viewBox="0 0 18 18"><circle cx="9" cy="9" r="9" fill="#fff"/><path d="M5 9l3 3 5-6" fill="none" stroke="#1a8ad8" stroke-width="2.4"/></svg>Optimized Payments</h3>
      <p>Vestibulum feugiat augue vitae velit ornare, vel auctor turpis vehicula. Suspendisse dictum accumsan risus a tempor. Morbi finibus nunc justo.</p>
    </div>
    <div class="feature">
      <h3><svg width="18" height="18" viewBox="0 0 18 18"><circle cx="9" cy="9" r="9" fill="#fff"/><path d="M5 9l3 3 5-6" fill="none" stroke="#1a8ad8" stroke-width="2.4"/></svg>Flexible Architecture</h3>
      <p>Curabitur et pretium dui. Quisque enim lorem, aliquet quis ante vitae, semper mattis leo. Phasellus sed diam id lacus tristique euismod vel ut velit.</p>
    </div>
  </div>
</section>

<section class="partners">
  <h2 class="section-title">Our Partners</h2>
  <div class="partner-row">
    <div class="partner-mark" role="img" aria-label="Partner badge"></div>
    <div class="partner-mark round" role="img" aria-label="Partner badge"></div>
    <div class="partner-mark" role="img" aria-label="Partner badge"></div>
    <div class="partner-mark" role="img" aria-label="Partner badge"></div>
    <div class="partner-mark" role="img" aria-label="Partner badge"></div>
    <div class="partner-mark" role="img" aria-label="Partner badge"></div>
    <div class="partner-mark" role="img" aria-label="Partner badge"></div>
  </div>
</section>

<section class="testimonials">
  <h2 class="section-title">What Our Customers Say?</h2>
  <div class="quotes">
    <div class="quote">
      <div class="quote-body">
        <div class="avatar" role="img" aria-label="Portrait photo of the customer"></div>
        <p>Sed elementum, odio eget consequat malesuada, sapien magna sagittis mauris, eu sodales augue nisl at mauris. Phasellus non hendrerit urna. Sed eget elit vehicula, convallis velit ut.</p>
      </div>
      <p class="quote-by"><strong>Owen Hale</strong> Lorem ipsum dolor sit amet</p>
    </div>
    <div class="quote">
      <div class="quote-body">
        <div class="avatar" role="img" aria-label="Portrait photo of the customer"></div>
        <p>Nullam eros neque, tincidunt vitae pellentesque sed, sollicitudin vel tellus. Aenean sit amet vulputate massa, in pretium orci. Morbi imperdiet lacus a ipsum porttitor euismod.</p>
      </div>
      <p class="quote-by"><strong>Rick Dorn</strong> Etiam turpis velit, bibendum males</p>
    </div>
  </div>
</section>

<section class="closing">
  <p>Our company has been in alternative payments for nearly 10 years and have strong products in Europe in the</p>
  <h2>PrePaid Zelo/TrevinCard and Voucher space.</h2>
  <div class="card-row">
    <span class="card-chip" role="img" aria-label="Accepted card"></span>
    <span class="card-chip" role="img" aria-label="Accepted card"></span>
    <span class="card-chip" role="img" aria-label="Accepted card"></span>
    <span class="card-chip" role="img" aria-label="Accepted card"></span>
  </div>
  <a class="btn" href="#">Get Started Now</a>
</section>

<footer class="site-footer">
  <div class="wrap">
    <div class="brand">Fenwu</div>
    <div class="footer-meta">
      <div><a href="#">Privacy Policy</a><a href="#">Sitemap</a></div>
      <div>Copyrights@2016 Fenwu. All Right Reserved.</div>
    </div>
    <div class="social">
      <span role="img" aria-label="Social link"></span>
      <span role="img" aria-label="Social link"></span>
      <span role="img" aria-label="Social link"></span>
      <span role="img" aria-label="Social link"></span>
    </div>
  </div>
</footer>

</body>
</html>
```